For Lease Sign to Attract National Retail Tenants

Attached is a logo design that was created by Pixel Harbor. I will like to develop a leasing sign that is 4 foot wide by 4 foot high or 4 feet wide and 6 feet high. I would like the sign to have a black background and use the colors that are in the logo. These will be signs that are placed in front of shopping centers and are often read by passing motorist so the sign must be simple, clean, very easy to read, distinctive, and have as few words as possible. It would be good if small amounts of bright green can be added as a boarder or ????? The text should be FOR LEASE, 415-738-2916, Rod Kellaway. I will want to also design cards and letter head around the same theme.

Target Market(s)

National retail tenants wanting to lease space in my shopping centers

Industry/Entity Type

Real Estate Development

Contact Information for Business Card

Tall Oak Holdings, LLC Rod Kellaway President & CEO 4127 Marlow Ave. Suite 308 La Jolla, CA 92037 415-738-2916 rodkellaway@quillpost.net

```html
<!DOCTYPE html>
<html lang="en">
<head>
<meta charset="utf-8">
<title>Tall Oak Holdings — Letterhead</title>
<link href="https://fonts.googleapis.com/css2?family=Arimo:wght@400;700&family=Cinzel:wght@700&display=swap" rel="stylesheet">
<style>
  :root {
    --backdrop: #e9e4e4;
    --paper: #ffffff;
    --brand-red: #c8161d;
    --rule-grey: #b9bcc2;
    --ink: #1e1e1e;
    --muted: #7d7d7d;
  }
  * { box-sizing: border-box; margin: 0; padding: 0; }
  html, body { width: 1200px; height: 784px; overflow: hidden; background: var(--backdrop); }
  .canvas { position: relative; width: 1200px; height: 784px; }
  .letterhead {
    position: absolute; left: 340px; top: 22px; width: 520px; height: 740px;
    background: var(--paper); box-shadow: 0 6px 22px rgba(0,0,0,.12);
    font-family: "Arimo", Arial, sans-serif; color: var(--ink);
  }
  .rule { position: absolute; }
  .rule--grey-top { left: 0; top: 0; width: 86px; height: 4px; background: var(--rule-grey); }
  .rule--red-top { left: 176px; top: 50px; right: 0; height: 4px; background: var(--brand-red); }
  .rule--grey-bottom { left: 0; bottom: 18px; width: 52px; height: 4px; background: var(--rule-grey); }
  .rule--red-bottom { left: 56px; bottom: 18px; right: 0; height: 4px; background: var(--brand-red); }
  .brand {
    position: absolute; left: 86px; top: 30px; display: flex; align-items: center; gap: 6px;
    font-family: "Cinzel", Georgia, serif; font-weight: 700; font-size: 15px;
    letter-spacing: 1px; color: var(--brand-red); white-space: nowrap;
  }
  .brand__mark { width: 9px; height: 9px; background: var(--brand-red); }
  .offer {
    position: absolute; right: 22px; top: 64px;
    font-family: "Cinzel", Georgia, serif; font-weight: 700; font-size: 15px;
    letter-spacing: 2px; color: var(--brand-red); white-space: nowrap;
  }
  .contact {
    position: absolute; right: 22px; top: 88px; width: 300px;
    font-size: 7.5px; color: var(--muted); line-height: 1.6; text-align: right;
  }
  .contact__row { display: flex; justify-content: flex-end; gap: 8px; white-space: nowrap; }
  .contact__item { display: inline-flex; align-items: center; gap: 3px; }
  .contact__icon { width: 7px; height: 7px; flex: none; }
  .body-copy {
    position: absolute; left: 62px; top: 132px; width: 400px;
    font-size: 10.5px; line-height: 1.42;
  }
  .body-copy p { margin-bottom: 14px; text-indent: 80px; }
</style>
</head>
<body>
<div class="canvas">
  <article class="letterhead">
    <div class="rule rule--grey-top"></div>
    <div class="brand"><span class="brand__mark"></span>TALL OAK</div>
    <div class="rule rule--red-top"></div>

    <div class="offer">For LEASE</div>
    <div class="contact">
      <div class="contact__row">
        <span class="contact__item">
          <svg class="contact__icon" viewBox="0 0 10 10"><circle cx="5" cy="5" r="5" fill="#c8161d"/><circle cx="5" cy="4" r="1.6" fill="#fff"/></svg>
          Suite 308, 3rd Floor, 4127 Marlow Ave, La Jolla 92037
        </span>
      </div>
      <div class="contact__row">
        <span class="contact__item">
          <svg class="contact__icon" viewBox="0 0 10 10"><circle cx="5" cy="5" r="5" fill="#c8161d"/><rect x="3.5" y="2.5" width="3" height="5" rx=".6" fill="#fff"/></svg>
          415 738 2916
        </span>
        <span class="contact__item">
          <svg class="contact__icon" viewBox="0 0 10 10"><circle cx="5" cy="5" r="5" fill="#c8161d"/><rect x="3" y="3" width="4" height="4" fill="#fff"/></svg>
          415 738 2917
        </span>
        <span class="contact__item">
          <svg class="contact__icon" viewBox="0 0 10 10"><circle cx="5" cy="5" r="5" fill="#c8161d"/><rect x="2.5" y="3.5" width="5" height="3" fill="#fff"/></svg>
          415 738 2918
        </span>
      </div>
      <div class="contact__row">
        <span class="contact__item">
          <svg class="contact__icon" viewBox="0 0 10 10"><circle cx="5" cy="5" r="5" fill="#c8161d"/><rect x="2.5" y="3" width="5" height="4" fill="#fff"/></svg>
          info@talloakholdings.com
        </span>
        <span class="contact__item">
          <svg class="contact__icon" viewBox="0 0 10 10"><circle cx="5" cy="5" r="5" fill="#c8161d"/><circle cx="5" cy="5" r="2.2" fill="none" stroke="#fff" stroke-width="1"/></svg>
          www.talloakholdings.com
        </span>
      </div>
    </div>

    <div class="body-copy">
      <p>Lorem Ipsum is simply dummy text of the printing and typesetting industry. Lorem Ipsum has been the industry's standard dummy text ever since the 1500s, when an unknown printer took a galley of type and scrambled it to make a type specimen book. It has survived not only five centuries, but also the leap into electronic typesetting, remaining essentially unchanged. It was popularised in the 1960s with the release of Typeline sheets containing Lorem Ipsum passages, and more recently with desktop publishing software like Folio Composer including versions of Lorem Ipsum.</p>
      <p>It is a long established fact that a reader will be distracted by the readable content of a page when looking at its layout. The point of using Lorem Ipsum is that it has a more-or-less normal distribution of letters, as opposed to using 'Content here, content here', making it look like readable English. Many desktop publishing packages and web page editors now use Lorem Ipsum as their default model text, and a search for 'lorem ipsum' will uncover many web sites still in their infancy. Various versions have evolved over the years, sometimes by accident, sometimes on purpose (injected humour and the like).</p>
      <p>Contrary to popular belief, Lorem Ipsum is not simply random text. It has roots in a piece of classical Latin literature from 45 BC, making it over 2000 years old. Edwin Marlowe, a Latin professor at Ashcombe College in Virginia, looked up one of the more obscure Latin words, consectetur, from a Lorem Ipsum passage, and going through the cites of the word in classical literature, discovered the undoubtable source. Lorem Ipsum comes from sections 1.10.32 and 1.10.33 of "de Finibus Bonorum et Malorum" structures, to generate Lorem Ipsum which looks reasonable. The generated Lorem Ipsum is therefore always free from repetition, injected humour, or non-characteristic words etc.</p>
    </div>

    <div class="rule rule--grey-bottom"></div>
    <div class="rule rule--red-bottom"></div>
  </article>
</div>
</body>
</html>
```